Stationery for Villa Marenta Design Hotel**

Who we are:

Wander on an isolated beach while breathing in the fresh, salty, sea air. Listen to the warm Pacific wind rustling through green palm trees as you walk to a pristine lagoon. Feel the delicious warmth of the sun kiss your skin; the beach is yours. At Villa Marenta you can experience a vacation in undisturbed, natural beauty. We have created a place for you to find new strength, relaxation, and inner harmony. We offer total rest to the experienced traveler from all over the world.

We are a brand new and smartly built design-hotel (under construction) close to a unique beach and a fantastic surf spot in Huatulco, Southwest Mexico.

As you can see in the attachments, we do have an established corporate design, but as for now still need a format for booklets for information around our hotel and things to do in the area, important numbers (we fill in the content for that one).

Our corporate colors:
green #64b445, brown #b07043, blue #0ab7cf, yellow # f9b02a and #fcc01a, navy #444f69
Corporate fonts:
Krub and Miller Banner.
For further information access:
www.villamarenta.example
https://slidevault.example/view/QmPxLwZrTyKsNbVcHdJe/

Social Media: VillaMarenta

Industry/Entity Type

Hotel

Font styles to use
Other font styles liked:
• Krub, Miller Banner

Requirements
Must have
• Stick to Logo Design, defined corporate elements, logo, colors, fonts and general touch and feel
Nice to have
• Who we are:

Our corporate colors:
Corporate fonts:
Krub and Miller Banner.
www.villamarenta.example

Social Media: VillaMarenta

```html
<!DOCTYPE html>
<html lang="en">
<head>
<meta charset="utf-8">
<title>Villa Marenta – Business Cards</title>
<link rel="stylesheet" href="https://fonts.googleapis.com/css2?family=Open+Sans:wght@400;600;700&family=PT+Serif:wght@400&display=swap">
<style>
  :root {
    --stage: #2a2d31;
    --card: #2d2d2f;
    --card-facet: #1f1f21;
    --card-light: #3a3a3d;
    --gold: #f9b02a;
    --gold-deep: #e3a21f;
    --text: #f2f2f2;
    --muted: #c9c9c9;
  }
  * { margin: 0; padding: 0; box-sizing: border-box; }
  html, body { width: 1200px; height: 900px; overflow: hidden; }
  body {
    background: var(--stage);
    position: relative;
    font-family: "Open Sans", sans-serif;
  }
  .card {
    position: absolute;
    background: var(--card);
    border-radius: 22px;
    overflow: hidden;
    box-shadow: 0 18px 40px rgba(0,0,0,.45);
  }
  .card-facets { position: absolute; inset: 0; width: 100%; height: 100%; }
  .card--back { left: 150px; top: 170px; width: 320px; height: 560px; }
  .card--front { left: 530px; top: 290px; width: 560px; height: 320px; }

  .brand {
    position: absolute;
    display: flex;
    align-items: center;
    gap: 10px;
    color: var(--gold);
    font-weight: 600;
    letter-spacing: .04em;
    text-transform: uppercase;
  }
  .brand-mark { border: 2px solid var(--gold); flex: none; }
  .brand-coords {
    position: absolute;
    color: var(--gold);
    font-size: 8px;
    letter-spacing: .12em;
  }
  .card--back .brand { left: 30px; top: 44px; font-size: 17px; }
  .card--back .brand-mark { width: 22px; height: 22px; }
  .card--back .brand-coords { left: 30px; top: 76px; font-size: 6.5px; }

  .card--front .brand { left: 150px; top: 132px; font-size: 30px; }
  .card--front .brand-mark { width: 36px; height: 36px; }
  .card--front .brand-coords { left: 150px; top: 186px; font-size: 9px; }

  .person { position: absolute; left: 96px; top: 250px; }
  .person-name { color: var(--gold); font-weight: 700; font-size: 23px; line-height: 1.1; }
  .person-role { color: var(--text); font-size: 14px; margin-top: 2px; }

  .contact {
    position: absolute;
    left: 76px; top: 330px;
    list-style: none;
    font-family: "PT Serif", serif;
    color: var(--text);
    font-size: 14.5px;
    line-height: 1.45;
  }
  .contact li { display: flex; gap: 8px; align-items: flex-start; margin-bottom: 4px; }
  .contact-icon {
    flex: none;
    width: 15px; height: 15px;
    margin-top: 3px;
    background: var(--gold);
    border-radius: 2px;
  }
</style>
</head>
<body>

  <section class="card card--back" aria-label="Business card, contact side">
    <svg class="card-facets" viewBox="0 0 320 560" preserveAspectRatio="none" aria-hidden="true">
      <polygon points="0,240 0,560 210,560" fill="var(--card-facet)"/>
      <polygon points="150,0 320,0 320,330" fill="var(--card-light)" opacity=".35"/>
      <polygon points="0,240 60,560 0,560" fill="#000" opacity=".2"/>
    </svg>

    <div class="brand"><span class="brand-mark"></span>Villa Marenta</div>
    <div class="brand-coords">MEXICO · 15°44'08"N 96°07'51"W</div>

    <div class="person">
      <p class="person-name">Example Name</p>
      <p class="person-role">Designation</p>
    </div>

    <ul class="contact">
      <li>
        <svg class="contact-icon" viewBox="0 0 16 16" aria-hidden="true"><path d="M8 3a3 3 0 0 0-3 3c0 2.3 3 6 3 6s3-3.7 3-6a3 3 0 0 0-3-3zm0 4.2A1.2 1.2 0 1 1 8 4.8a1.2 1.2 0 0 1 0 2.4z" fill="#2d2d2f"/></svg>
        <span>Villa Marenta, Playa Serena,<br>Huatulco, Oaxaca, Mexiko</span>
      </li>
      <li>
        <svg class="contact-icon" viewBox="0 0 16 16" aria-hidden="true"><path d="M5 3.5l1.8 2.2-1 1.2a7 7 0 0 0 3.3 3.3l1.2-1L12.5 11l-1.2 1.5C7.5 12.3 3.7 8.5 3.5 4.7z" fill="#2d2d2f"/></svg>
        <span>+52 1 (958) 410 7325</span>
      </li>
      <li>
        <svg class="contact-icon" viewBox="0 0 16 16" aria-hidden="true"><path d="M3 5h10v6H3z M3 5l5 4 5-4" fill="none" stroke="#2d2d2f" stroke-width="1.3"/></svg>
        <span>hello@villamarenta.example</span>
      </li>
      <li>
        <svg class="contact-icon" viewBox="0 0 16 16" aria-hidden="true"><circle cx="8" cy="8" r="4.5" fill="none" stroke="#2d2d2f" stroke-width="1.2"/><path d="M3.5 8h9M8 3.5c-2 2.5-2 6.5 0 9M8 3.5c2 2.5 2 6.5 0 9" fill="none" stroke="#2d2d2f" stroke-width="1"/></svg>
        <span>www.villamarenta.example</span>
      </li>
    </ul>
  </section>

  <section class="card card--front" aria-label="Business card, brand side">
    <svg class="card-facets" viewBox="0 0 560 320" preserveAspectRatio="none" aria-hidden="true">
      <polygon points="0,0 230,0 0,200" fill="var(--card-light)" opacity=".35"/>
      <polygon points="380,320 560,90 560,320" fill="var(--card-facet)"/>
    </svg>

    <div class="brand"><span class="brand-mark"></span>Villa Marenta</div>
    <div class="brand-coords">MEXICO · 15°44'08"N 96°07'51"W</div>
  </section>

</body>
</html>
```